Accounting firm needing business card / letterhead designed
Marcus L. Trenholm, CPA
marcus@veltrowledger.com
www.veltrowledger.com
842 E Alder Ave Perrysburg, OH 43827
419-562-0974

```html
<!DOCTYPE html>
<html lang="en">
<head>
<meta charset="utf-8">
<title>Veltro Ledger – Business Card</title>
<link href="https://fonts.googleapis.com/css2?family=Open+Sans:wght@400;600;700&display=swap" rel="stylesheet">
<style>
  :root {
    --navy: #27216a;
    --green: #7dbb35;
    --white: #ffffff;
    --paper: #f3f3f4;
    --backdrop: #2b2b2d;
  }
  * { margin: 0; padding: 0; box-sizing: border-box; }
  html, body {
    width: 1200px; height: 904px; overflow: hidden;
    background: var(--backdrop);
    font-family: "Open Sans", sans-serif;
  }
  .sheet {
    width: 1200px; height: 904px;
    display: flex; flex-direction: column;
    align-items: center; justify-content: center; gap: 40px;
  }
  .card {
    position: relative;
    width: 700px; height: 400px;
    overflow: hidden;
    box-shadow: 0 12px 30px rgba(0,0,0,.45);
  }
  .card--front {
    background: var(--navy);
    display: flex; align-items: center; justify-content: center;
  }
  .wordmark {
    font-weight: 600;
    letter-spacing: 6px;
    text-transform: uppercase;
    line-height: 1;
  }
  .card--front .wordmark { color: var(--white); font-size: 46px; }
  .card--back {
    background: linear-gradient(135deg, var(--white) 0%, var(--paper) 60%, #e4e4e6 100%);
  }
  .card__panel { position: absolute; inset: 0; }
  .card--back .wordmark {
    position: absolute; left: 36px; top: 250px;
    color: var(--navy); font-size: 34px;
  }
  .contact {
    position: absolute; left: 400px; top: 70px;
    color: var(--white);
  }
  .contact__name {
    color: var(--green); font-weight: 700; font-size: 23px;
    margin-bottom: 18px;
  }
  .contact__address { font-size: 15px; line-height: 1.4; margin-bottom: 22px; padding-left: 4px; }
  .contact__list { list-style: none; padding-left: 4px; }
  .contact__item {
    display: flex; align-items: center; gap: 10px;
    font-size: 15px; line-height: 1; margin-bottom: 10px;
  }
  .contact__icon { width: 16px; height: 16px; flex: none; }
</style>
</head>
<body>
<main class="sheet">
  <section class="card card--front" aria-label="Card front">
    <span class="wordmark">Veltro Ledger</span>
  </section>

  <section class="card card--back" aria-label="Card back">
    <svg class="card__panel" width="700" height="400" viewBox="0 0 700 400" aria-hidden="true">
      <polygon points="350,0 700,0 700,400 600,400 315,215" fill="var(--navy)"/>
      <polyline points="350,-4 315,215 606,404" fill="none" stroke="var(--green)" stroke-width="8"/>
    </svg>

    <span class="wordmark">Veltro Ledger</span>

    <div class="contact">
      <p class="contact__name">Marcus L. Trenholm, CPA</p>
      <p class="contact__address">842 E Alder Ave Perrysburg<br>OH 43827</p>
      <ul class="contact__list">
        <li class="contact__item">
          <svg class="contact__icon" viewBox="0 0 16 16" aria-hidden="true"><path d="M3 1.5l3 3-1.6 1.8a9 9 0 0 0 5.3 5.3L11.5 10l3 3-1.8 2C7 15 1 9 1 3.3z" fill="var(--green)"/></svg>
          419-562-0974
        </li>
        <li class="contact__item">
          <svg class="contact__icon" viewBox="0 0 16 16" aria-hidden="true"><rect x="1" y="3" width="14" height="10" rx="1.5" fill="var(--green)"/><path d="M1.5 4l6.5 5 6.5-5" fill="none" stroke="var(--navy)" stroke-width="1.3"/></svg>
          marcus@veltrowledger.com
        </li>
        <li class="contact__item">
          <svg class="contact__icon" viewBox="0 0 16 16" aria-hidden="true"><circle cx="8" cy="8" r="7" fill="var(--green)"/><g fill="none" stroke="var(--navy)" stroke-width="1"><ellipse cx="8" cy="8" rx="3" ry="7"/><path d="M1 8h14M2.5 4.5h11M2.5 11.5h11"/></g></svg>
          www.veltrowledger.com
        </li>
      </ul>
    </div>
  </section>
</main>
</body>
</html>
```